Business Card Design

Buy and sell properties
Buy and rehab properties
Buy properties for cash
That is what I do but do need a logo
looking for some type of logo or design on it
Just started business
Back of card should say something like BUY HOUSES CASH
Overview: it is a new company. Basically I buy properties wholesale and fix them up and sell them or sell them to other fix and flippers
Background: company is new so not any background
Market: is basically anyone selling a house or buying a house. Someone that needs to sell house fast. Basically I am a cash home buyer!!!

Updates
Email on card should be:   harborlanerealtyinc@mailnest.com

Industry/Entity Type
House
Contact Information for Business Card
Harbor Lane Realty Inc
PO Box 718296
Coral Mill Key FL 33071

Dwight Kallum
harborlanerealtyinc@mailnest.com
305-271-5589

```html
<!DOCTYPE html>
<html lang="en">
<head>
<meta charset="utf-8">
<title>Harbor Lane Realty Inc — Business Card</title>
<link rel="stylesheet" href="https://fonts.googleapis.com/css2?family=Exo+2:wght@300;400;600;700&display=swap">
<style>
  :root {
    --backdrop: #e9e6e1;
    --card-black: #0b0b0b;
    --card-charcoal: #2a2a2a;
    --text-white: #f4f4f4;
    --text-soft: #d9d9d9;
    --accent-green: #8fdc4e;
    --accent-green-deep: #5fb52a;
    --band-text: #101010;
  }
  * { box-sizing: border-box; margin: 0; padding: 0; }
  html, body {
    width: 1200px; height: 818px; overflow: hidden;
    background: var(--backdrop);
    font-family: "Exo 2", sans-serif;
  }
  .canvas {
    width: 1200px; height: 818px;
    display: flex; align-items: center; justify-content: center;
  }
  .card {
    position: relative;
    width: 420px; height: 735px;
    border-radius: 6px;
    overflow: hidden;
    background: radial-gradient(ellipse at 50% 45%, var(--card-charcoal) 0%, var(--card-black) 70%);
    box-shadow: 0 10px 30px rgba(0,0,0,0.25);
    color: var(--text-white);
  }
  .brand {
    position: absolute; top: 150px; left: 0; right: 0;
    display: flex; align-items: center; justify-content: center; gap: 12px;
  }
  .brand-mark {
    width: 16px; height: 16px;
    background: var(--accent-green);
  }
  .brand-name {
    font-weight: 300;
    font-size: 30px;
    letter-spacing: 0.5px;
    color: var(--text-white);
    white-space: nowrap;
  }
  .person-name {
    position: absolute; top: 262px; left: 30px; right: 30px;
    text-align: right;
    font-weight: 600;
    font-size: 38px;
    letter-spacing: 1px;
    white-space: nowrap;
  }
  .contact {
    position: absolute; top: 350px; left: 24px; right: 30px;
    list-style: none;
    text-align: right;
    font-weight: 300;
    font-size: 20px;
    line-height: 34px;
    color: var(--text-soft);
    white-space: nowrap;
  }
  .contact .address { margin-top: 4px; }
  .tagline-band {
    position: absolute; left: 0; right: 0; bottom: 0;
    height: 108px;
    background: linear-gradient(180deg, var(--accent-green) 0%, var(--accent-green-deep) 100%);
    border-top: 6px solid var(--card-black);
    display: flex; align-items: center; justify-content: center;
  }
  .tagline-band::before {
    content: "";
    position: absolute; left: 0; right: 0; top: -12px;
    height: 3px; background: var(--accent-green);
  }
  .tagline {
    font-weight: 700;
    font-size: 30px;
    letter-spacing: 1px;
    color: var(--band-text);
  }
</style>
</head>
<body>
  <main class="canvas">
    <article class="card">
      <header class="brand">
        <span class="brand-mark"></span>
        <span class="brand-name">Harbor Lane Realty Inc</span>
      </header>
      <h1 class="person-name">Dwight Kallum</h1>
      <ul class="contact">
        <li class="phone">305-271-5589</li>
        <li class="email">harborlanerealtyinc@mailnest.com</li>
        <li class="address">PO Box 718296 Coral Mill Key FL 33071</li>
      </ul>
      <footer class="tagline-band">
        <span class="tagline">BUY HOUSES CASH</span>
      </footer>
    </article>
  </main>
</body>
</html>
```